RW Framewell Inc Business cards

We need business cards using our existing logo but slightly modified. Right now the logo says RW Loadbearing Masonry. We want to keep the RW part of the design, but replace the Structural Concrete portion with "FRAMEWELL". Please see the attached file.
Ideally this would be a blank template so we can add Different Names, titles, and phone numbers later.
On the one side we want only the logo and on the other side the detail. I'm attaching an example for you to see.
Please reach out with any other questions. Our address and other details will be given out once we find a design we like.

Target Market(s)

Construction Industry

```html
<!DOCTYPE html>
<html lang="en">
<head>
<meta charset="utf-8">
<title>RW Framewell Inc – Business Cards</title>
<link rel="stylesheet" href="https://fonts.googleapis.com/css2?family=Montserrat:wght@600;700&family=Roboto:wght@400;500&display=swap">
<style>
  :root {
    --backdrop: #3d3d3f;
    --card: #1c1c1e;
    --logo-front: #6e6e72;
    --blue: #3a6fb8;
    --white: #f4f4f4;
    --faint: #262628;
  }
  * { box-sizing: border-box; margin: 0; padding: 0; }
  html, body { width: 799px; height: 1200px; overflow: hidden; }
  body {
    background: var(--backdrop);
    position: relative;
    font-family: "Roboto", Arial, sans-serif;
  }
  .card {
    position: absolute;
    left: 80px;
    width: 640px;
    height: 366px;
    background: var(--card);
    border-radius: 4px;
    box-shadow: 0 14px 30px rgba(0,0,0,.45);
    overflow: hidden;
  }
  .card--front { top: 110px; }
  .card--back { top: 724px; }

  .wordmark { position: absolute; font-family: "Montserrat", Arial, sans-serif; font-weight: 700; text-align: center; }
  .wordmark__initials { display: block; line-height: 1; }
  .wordmark__name { display: block; letter-spacing: .22em; }

  .card--front .wordmark { left: 0; right: 0; top: 92px; color: var(--logo-front); }
  .card--front .wordmark__initials { font-size: 130px; }
  .card--front .wordmark__name { font-size: 34px; margin-top: 4px; }

  .card--back .faint-mark {
    position: absolute; right: 40px; top: 70px;
    font-family: "Montserrat", Arial, sans-serif; font-weight: 700;
    font-size: 170px; line-height: 1; color: var(--faint);
  }
  .card--back .wordmark { right: 36px; bottom: 34px; color: var(--white); text-align: right; }
  .card--back .wordmark__initials { font-size: 84px; }
  .card--back .wordmark__name { font-size: 24px; margin-top: 4px; }

  .tab {
    position: absolute; left: -22px; top: 22px;
    width: 44px; height: 58px; border-radius: 50%;
    background: var(--blue);
  }
  .person { position: absolute; left: 40px; top: 30px; }
  .person__name { color: var(--blue); font-family: "Montserrat", Arial, sans-serif; font-weight: 600; font-size: 20px; }
  .person__title { color: var(--white); font-size: 14px; margin-top: 4px; }

  .contact { position: absolute; left: 28px; top: 168px; color: var(--white); font-size: 15px; }
  .contact__address { line-height: 1.35; padding-left: 10px; }
  .contact__rule { width: 210px; height: 1.5px; background: var(--blue); margin: 8px 0 8px 10px; }
  .contact__list { list-style: none; }
  .contact__list li { display: flex; align-items: center; gap: 10px; line-height: 1.5; }
  .contact__list svg { width: 13px; height: 13px; fill: var(--blue); flex: none; }
</style>
</head>
<body>

  <section class="card card--front" aria-label="Card front">
    <div class="wordmark">
      <span class="wordmark__initials">RW</span>
      <span class="wordmark__name">FRAMEWELL</span>
    </div>
  </section>

  <section class="card card--back" aria-label="Card back">
    <span class="faint-mark" aria-hidden="true">RW</span>
    <span class="tab" aria-hidden="true"></span>

    <div class="person">
      <p class="person__name">Daniel RW Hart</p>
      <p class="person__title">Managing Director</p>
    </div>

    <div class="contact">
      <p class="contact__address">88 Sample Ave., Any Town,<br>Oregon, US 654321</p>
      <div class="contact__rule"></div>
      <ul class="contact__list">
        <li><svg viewBox="0 0 16 16"><path d="M3 1h3l1.5 4-2 1.3a9 9 0 0 0 4.2 4.2L11 8.5l4 1.5v3a2 2 0 0 1-2 2A12 12 0 0 1 1 3a2 2 0 0 1 2-2z"/></svg>555-010-2020</li>
        <li><svg viewBox="0 0 16 16"><path d="M1 3h14v10H1z M1 3l7 6 7-6" fill="none" stroke="#3a6fb8" stroke-width="1.6"/></svg>dan@sitename.com</li>
        <li><svg viewBox="0 0 16 16"><circle cx="8" cy="8" r="7"/></svg>www.sitename.com</li>
      </ul>
    </div>

    <div class="wordmark">
      <span class="wordmark__initials">RW</span>
      <span class="wordmark__name">FRAMEWELL</span>
    </div>
  </section>

</body>
</html>
```